Awesome photographers card for an awesome new business

Double sided business card Black background and silver logo in middle on one side. Details on otherside. please keep it simple

Industry/Entity Type

Photographer

Contact Information for Business Card

Gerald Fenwick
0452817360
GeraldFenwickPhotography47@mailbox.test
www.GeraldFenwickPhotography.test.au
Instagram _Gerald_fenwick

Requirements
Must have
• My logo in Silver
• please use instagram logo instead of "Instagram"

```html
<!DOCTYPE html>
<html lang="en">
<head>
<meta charset="utf-8">
<title>Gerald Fenwick Photography – Business Card</title>
<link rel="stylesheet" href="https://fonts.googleapis.com/css2?family=Open+Sans:wght@300;400;700&display=swap">
<style>
  :root {
    --stage: #2b2b2d;
    --card: #fafafa;
    --ink: #3a3a3a;
    --ink-soft: #6e6e6e;
    --silver: #8f8f8f;
    --silver-light: #c4c4c4;
    --band-dark: #7d7d7d;
    --band-light: #b9b9b9;
    --rule: #9a9a9a;
  }
  * { box-sizing: border-box; margin: 0; padding: 0; }
  html, body {
    width: 1200px; height: 900px; overflow: hidden;
    background: var(--stage);
    font-family: "Open Sans", Arial, sans-serif;
  }
  .stage {
    width: 1200px; height: 900px;
    display: flex; flex-direction: column;
    align-items: center; justify-content: center; gap: 60px;
  }
  .card {
    position: relative;
    width: 600px; height: 343px;
    background: var(--card);
    overflow: hidden;
  }

  /* Front */
  .front .wordmark {
    position: absolute; left: 0; right: 0; top: 120px;
    text-align: center;
    font-weight: 300; font-size: 44px; color: var(--silver);
    letter-spacing: 1px;
  }
  .front .site {
    position: absolute; left: 0; right: 0; top: 258px;
    text-align: center;
    font-size: 13px; color: var(--ink-soft); letter-spacing: 2.4px;
  }

  /* Back */
  .back .badge {
    position: absolute; right: 40px; top: 28px;
    display: flex; align-items: center; gap: 10px;
  }
  .back .badge-circle {
    width: 22px; height: 22px; border-radius: 50%;
    background: var(--silver-light);
  }
  .back .badge-name {
    font-weight: 300; font-size: 22px; color: var(--silver);
  }
  .back .divider {
    position: absolute; left: 30px; right: 30px; top: 132px;
    height: 1px; background: var(--rule);
  }
  .back .contact {
    position: absolute; left: 40px; top: 180px;
  }
  .back .person {
    font-weight: 700; font-size: 17px; color: var(--ink);
    letter-spacing: 0.3px; margin-bottom: 6px;
  }
  .back .line {
    display: flex; align-items: center; gap: 8px;
    font-size: 12.5px; color: var(--ink); line-height: 18px;
  }
  .back .line svg { width: 11px; height: 11px; flex: none; }
  .back .band { position: absolute; left: 0; bottom: 0; width: 600px; height: 70px; }
  .back .band-site {
    position: absolute; left: 40px; bottom: 14px;
    font-size: 14px; color: #ffffff; letter-spacing: 0.3px;
  }
</style>
</head>
<body>
<main class="stage">

  <section class="card front" aria-label="Card front">
    <div class="wordmark">Gerald Fenwick</div>
    <div class="site">www.GeraldFenwickPhotography.test.au</div>
  </section>

  <section class="card back" aria-label="Card back">
    <div class="badge">
      <span class="badge-circle"></span>
      <span class="badge-name">Gerald Fenwick</span>
    </div>
    <div class="divider"></div>

    <div class="contact">
      <div class="person">GERALD FENWICK</div>
      <div class="line">
        <svg viewBox="0 0 12 12" aria-hidden="true"><path fill="#3a3a3a" d="M1 3.5C1 2 2.5 1.5 6 1.5S11 2 11 3.5V5H8.5V4H3.5V5H1Z M2.5 6h7l1 4.5h-9Z"/><circle cx="6" cy="8" r="1.3" fill="#fafafa"/></svg>
        <span>0452817360</span>
      </div>
      <div class="line">
        <svg viewBox="0 0 12 12" aria-hidden="true"><rect x="0.5" y="2.5" width="11" height="7.5" fill="#3a3a3a"/><path d="M0.8 2.8L6 7l5.2-4.2" fill="none" stroke="#fafafa" stroke-width="1"/></svg>
        <span>GeraldFenwickPhotography47@mailbox.test</span>
      </div>
      <div class="line">
        <svg viewBox="0 0 12 12" aria-hidden="true"><rect x="1" y="1" width="10" height="10" fill="#3a3a3a"/></svg>
        <span>Gerald_fenwick</span>
      </div>
    </div>

    <svg class="band" viewBox="0 0 600 70" aria-hidden="true">
      <defs>
        <linearGradient id="bandFill" x1="0" y1="0" x2="1" y2="0">
          <stop offset="0" stop-color="var(--band-dark)"/>
          <stop offset="1" stop-color="var(--band-light)"/>
        </linearGradient>
      </defs>
      <path d="M0 28 H400 C418 28 420 14 438 14 H600 V70 H0 Z" fill="url(#bandFill)"/>
      <path d="M0 22 H396 C414 22 416 8 434 8 H600" fill="none" stroke="var(--silver-light)" stroke-width="1.5"/>
    </svg>
    <div class="band-site">www.GeraldFenwickPhotography.test.au</div>
  </section>

</main>
</body>
</html>
```